one pager for investors

I will give an initial file in any format needed. Also, the photo that must be included. As well as the logo, that must be the key to the overall design in terms of font, colors, and general layout. I will attach a file in PDF format, which is a one pager presenting a project for investors that I would like to attract and convinced to invest in my project. What I would like you to do is propose me different and better design options, taking my first draft as an example. But you must absolutely keep every single word and number, absolutely all the information written in my first draft(except “ TEMPLATE DRAFT”). Also, on the top left corner is the logo of our company, which I think should be your main inspiration document is a one pager presented to potential investors that not only has to include the most important information in order for them to be able to see everything needed to see the value of the project (which I’ve already taken care of by writing the text needed, numbers presented and timeline shown; all of which which must be preserved in terms of content, but can be completely redesigned and manipulated ) sh a.k.a. Project summary for investor to go for it.
Serious rich investors
Real eatate

```html
<!DOCTYPE html>
<html lang="fr">
<head>
<meta charset="utf-8">
<title>Projet immobilier XXX – Résumé investisseur</title>
<link rel="stylesheet" href="https://fonts.googleapis.com/css2?family=Public+Sans:wght@400;500;600;700&display=swap">
<style>
  :root{
    --blue:#3a5aa3;
    --navy:#2b3f78;
    --navy-dark:#1e2d5c;
    --ink:#1d1d22;
    --muted:#555a66;
    --rule:#d3d9e6;
    --rule-strong:#6f86bd;
    --card-top:#f5f7fb;
    --card-bottom:#e3ebf6;
    --backdrop:#f1f1f1;
    --track:#d6d6d6;
  }
  *{box-sizing:border-box;margin:0;padding:0}
  html,body{width:1200px;height:1200px;overflow:hidden}
  body{background:var(--backdrop);font-family:"Public Sans",Arial,sans-serif;color:var(--ink)}
  .page{position:absolute;left:150px;top:0;width:900px;height:1200px;background:#fff;overflow:hidden}

  .top-band{position:absolute;left:0;top:0;width:900px;height:61px;background:var(--blue)}
  .doc-title{position:absolute;right:40px;top:18px;color:#fff;font-weight:700;font-size:20px;letter-spacing:.1px}

  .hero{position:absolute;left:0;top:61px;width:900px;height:492px;
    background:
      linear-gradient(180deg,rgba(20,20,24,0) 45%,rgba(20,20,24,.55) 75%,rgba(20,20,24,.8) 100%),
      linear-gradient(100deg,#b9b8b4 0%,#9a948c 30%,#7c6a5c 55%,#8f7d70 75%,#5f4d42 100%);}

  .brand{position:absolute;left:36px;top:0;width:325px;height:132px;background:#fff;display:flex;align-items:center;justify-content:center}
  .brand-name{color:#2a2a2e;font-weight:600;font-size:26px;line-height:1}

  .intro{position:absolute;left:36px;top:391px;width:800px;color:#fff}
  .intro h2{font-size:19px;font-weight:700;letter-spacing:.2px}
  .intro .bar{width:51px;height:3px;background:#fff;margin:13px 0 12px}
  .intro p{font-size:14px;line-height:20px;color:#f0f0f0}
  .duration{display:flex;align-items:center;gap:14px;margin-top:16px;font-weight:700;font-size:14.5px}

  .card{position:absolute;top:578px;width:410px}
  .card-head{height:62px;color:#fff;display:flex;align-items:center;gap:8px;padding-left:28px;font-weight:700;font-size:17px;position:relative}
  .card-head::after{content:"";position:absolute;left:0;bottom:-12px;border-top:12px solid var(--navy-dark);border-left:13px solid transparent}
  .card-body{margin-left:13px;border:1.5px solid var(--rule-strong);border-top:none;background:linear-gradient(180deg,var(--card-top),var(--card-bottom));padding:6px 17px 0}
  .row{display:flex;justify-content:space-between;align-items:center;border-bottom:1.5px solid var(--rule);font-size:12.5px;color:#222}
  .row.strong{font-weight:700}
  .row.sep{border-bottom-color:var(--rule-strong)}
  .row:last-child{border-bottom:none}
  .plan{left:23px}
  .plan .card-head{background:var(--blue)}
  .plan .row{height:31px}
  .invest{left:456px}
  .invest .card-head{background:var(--navy)}
  .invest .row{height:40px}

  .timeline{position:absolute;left:0;top:0;width:900px;height:1200px;pointer-events:none}
  .step{position:absolute;top:1104px;width:180px;margin-left:-90px;text-align:center}
  .step .date{font-weight:700;font-size:15px}
  .step .label{font-size:13px;color:#2b2b2b;margin-top:3px}

  .footer{position:absolute;left:36px;top:1170px;font-size:11px;color:#8a8d96}
  .footer b{color:var(--blue);font-weight:700;margin-right:6px}
  .footer .pipe{margin-right:6px}
  .page-tab{position:absolute;right:0;top:1161px;width:124px;height:39px;background:var(--blue);clip-path:polygon(12px 0,100% 0,100% 100%,0 100%);color:#fff;font-size:11.5px;display:flex;align-items:center;justify-content:flex-end;padding-right:28px}
  .page-tab::before{content:"";position:absolute;left:0;top:0;width:18px;height:39px;background:#4f8fe0;clip-path:polygon(12px 0,18px 0,6px 100%,0 100%)}
  .base-line{position:absolute;left:0;bottom:0;width:900px;height:3px;background:var(--blue)}
</style>
</head>
<body>
<div class="page">
  <div class="hero" role="img" aria-label="Rendu architectural d'un immeuble résidentiel moderne à balcons vitrés, entouré de verdure"></div>
  <div class="top-band"></div>
  <div class="doc-title">CONFIDENTIEL – Projet imobilier “XXX”</div>

  <div class="brand">
    <span class="brand-name">Veralis Properties SA</span>
  </div>

  <section class="intro">
    <h2>DESCRIPTION DU PROJET</h2>
    <div class="bar"></div>
    <p>Le projet XXX est un projet de dévloppement de 30 appartements de standing en PPE au centre de Lausanne. Le terrain a été sécurisé par la signature du vente à terme conditionnelle. L’objectif est d’obtenir le permis de construire, puis de ventre les lots. Dans un premier temps sur plan puis au fil de la construction. .</p>
    <div class="duration">
      <svg width="42" height="12" viewBox="0 0 42 12"><path d="M0 6H40M34 1L40 6L34 11" fill="none" stroke="#4a6ab8" stroke-width="1.5"/></svg>
      <span>Durée estimée du projet – 24 à 36 mois.</span>
    </div>
  </section>

  <section class="card plan">
    <div class="card-head">
      <svg width="36" height="36" viewBox="0 0 36 36"><circle cx="20" cy="16" r="13" fill="#fff"/><path d="M20 16V3A13 13 0 0 1 33 16Z" fill="#c9d5ee"/><circle cx="10" cy="22" r="7" fill="var(--blue)" stroke="#fff" stroke-width="2"/><text x="10" y="26" font-size="9" fill="#fff" text-anchor="middle" font-family="Arial">$</text></svg>
      Plan financier
    </div>
    <div class="card-body">
      <div class="row"><span>Prix du terrain</span><span>CHF 2’000’000</span></div>
      <div class="row"><span>Frais d’acquisition</span><span>CHF 100’000</span></div>
      <div class="row"><span>Coût de construction</span><span>CHF 2’500’000</span></div>
      <div class="row"><span>Divers &amp; imprévus</span><span>CHF 200’000</span></div>
      <div class="row strong sep"><span>Prix de revient total</span><span>CHF 4’800’000</span></div>
      <div class="row strong"><span>Prix de vente total</span><span>CHF 7’500’000</span></div>
      <div class="row sep"><span>Honoraires sur vente</span><span>CHF 190’000</span></div>
      <div class="row strong"><span>Marge projet</span><span>CHF 2’510’000</span></div>
      <div class="row strong"><span>En % sur prix de vente</span><span>33.47%</span></div>
    </div>
  </section>

  <section class="card invest">
    <div class="card-head">
      <svg width="40" height="38" viewBox="0 0 40 38"><circle cx="13" cy="25" r="11" fill="none" stroke="#fff" stroke-width="2.5"/><text x="13" y="30" font-size="13" fill="#fff" text-anchor="middle" font-family="Arial">$</text><rect x="26" y="28" width="12" height="3" fill="#fff"/><rect x="26" y="33" width="12" height="3" fill="#fff"/><path d="M30 24C30 16 28 10 22 6M30 24C31 16 34 10 38 4" fill="none" stroke="#fff" stroke-width="2.5"/></svg>
      Structure d’investissement
    </div>
    <div class="card-body">
      <div class="row"><span>Besoin de fonds propres</span><span>CHF 2’000’000</span></div>
      <div class="row"><span>Retour de fonds total</span><span>CHF 3’156’600</span></div>
      <div class="row strong"><span>Bénéfice net investisseur</span><span>CHF 1’656’600</span></div>
      <div class="row sep"><span>Soit 2/3 du bénéfice projet</span><span></span></div>
      <div class="row strong sep"><span>Multiple sur fonds propres</span><span>x1.83</span></div>
      <div class="row strong"><span>Rendement annualisé</span><span>41.4%</span></div>
      <div class="row"><span>Calcul sur 24 mois</span><span></span></div>
    </div>
  </section>

  <svg class="timeline" viewBox="0 0 900 1200" aria-hidden="true">
    <line x1="35" y1="1076" x2="864" y2="1076" stroke="var(--track)" stroke-width="3"/>
    <path d="M853 1066L864 1076L853 1086" fill="none" stroke="var(--track)" stroke-width="3"/>
    <g fill="var(--blue)">
      <circle cx="127" cy="1009" r="38"/><path d="M119 1043L127 1055L135 1043Z"/>
      <circle cx="558" cy="1009" r="38"/><path d="M550 1043L558 1055L566 1043Z"/>
    </g>
    <g fill="var(--navy)">
      <circle cx="342" cy="1009" r="38"/><path d="M334 1043L342 1055L350 1043Z"/>
      <circle cx="772" cy="1009" r="38"/><path d="M764 1043L772 1055L780 1043Z"/>
    </g>
    <g fill="#fff">
      <rect x="113" y="1005" width="6" height="14"/><path d="M121 1006H132L140 1010V1014L130 1019H121Z"/>
      <text x="134" y="1004" font-size="18" font-weight="700" font-family="Arial" text-anchor="middle">$</text>
      <path d="M329 994H344L351 1001V1024H329Z"/>
      <circle cx="348" cy="1016" r="6" fill="var(--navy)" stroke="#fff" stroke-width="2.5"/><path d="M352 1020L357 1025" stroke="#fff" stroke-width="3"/>
      <rect x="546" y="998" width="5" height="26"/><rect x="546" y="998" width="24" height="4"/><rect x="541" y="1010" width="14" height="5"/><path d="M566 1002V1018Q566 1022 562 1022" fill="none" stroke="#fff" stroke-width="2.5"/>
      <rect x="759" y="994" width="18" height="30"/><rect x="777" y="1006" width="9" height="18"/>
      <g fill="var(--navy)"><rect x="763" y="999" width="4" height="5"/><rect x="770" y="999" width="4" height="5"/><rect x="763" y="1008" width="4" height="5"/><rect x="770" y="1008" width="4" height="5"/><rect x="766" y="1016" width="5" height="8"/></g>
    </g>
    <g stroke="#c3cfe8" stroke-width="3">
      <circle cx="127" cy="1076" r="8" fill="var(--blue)"/>
      <circle cx="342" cy="1076" r="8" fill="var(--navy)"/>
      <circle cx="558" cy="1076" r="8" fill="var(--blue)"/>
      <circle cx="772" cy="1076" r="8" fill="var(--navy)"/>
    </g>
  </svg>

  <div class="step" style="left:127px"><div class="date">08.2024</div><div class="label">Achat parcelle</div></div>
  <div class="step" style="left:342px"><div class="date">04.2025</div><div class="label">Mise à l’enquête</div></div>
  <div class="step" style="left:558px"><div class="date">12.2025</div><div class="label">Début construction</div></div>
  <div class="step" style="left:772px"><div class="date">12.2025</div><div class="label">Livraison</div></div>

  <div class="footer"><b>CONFIDENTIEL</b><span class="pipe">|</span>Veralis Properties Vaud SA - Rue des Tilleuls 8 - CH-1099 Vernex</div>
  <div class="page-tab">Page 2</div>
  <div class="base-line"></div>
</div>
</body>
</html>
```